"Inkvale" printing shop

-The design must be based around the attached HPID (home page information design) called "Inkvale".

The table boxes are just for approximate placement of information – you DON'T have to box everything in and you can arrange these. All fonts used in the HPID are only examples - you can use any Google font you wish.

- Information only is in orange text. Copy to go on the design in black text. Some instructions are in the HPID. Please be creative!

-The design needs to be modern. Colours are to be consistent with their new logo or complement it. Keep it clean and simple, you don't need to use lots of colours. Use lots of white.

- images / icons for the site need to be relevant and high quality, but they must also be free images or icons. I have attached a few examples that could be used.

Width of content will be 1100 pixels when implemented as a web page. Header height (without nav bar) 150-200 pixels.

If your design is chosen the winning PSD file will have to be provided as follows…
1. Canvas size of 2000px x 2000px - 72ppi in Adobe Photoshop (CS5 compatible)
2. Width of content section is 1100px wide - centered in the canvas
3. Any button rollovers/hovers in the PSD as hidden layers.
4. All fonts used must be Google fonts.
5. You will need to supply the chosen home page plus one example page (example page as a style guide for how all other pages will look). Example page is only the header and navigational bar at the top, an empty sector in the middle with a column (190 px wide) which can be left or right aligned which means the main sector is 910 pixels wide, and then the footer at the bottom of the page

Checklist - http://pagebuildertally.example/

Examples of some websites that have great design... don't copy them please but they are similar in look to what we are after....
http://www.rookfenly.example/

Industry/Entity Type

Printing

Font styles to use
Serif
Sans Serif

Requirements
Should not have
• Drop shadows, comic sans font

```html
<!DOCTYPE html>
<html lang="en">
<head>
<meta charset="utf-8">
<title>Inkvale – Printing &amp; Photocopying</title>
<link href="https://fonts.googleapis.com/css2?family=Lato:wght@300;400;700&family=Josefin+Sans:wght@300;400&display=swap" rel="stylesheet">
<style>
:root{
  --green:#7db135;
  --ink:#222;
  --text:#333;
  --line:#e2e2e2;
  --grey-bg:#f0f0f0;
  --charcoal:#333333;
  --charcoal-dark:#2b2b2b;
  --btn-dark:#2f3340;
  --white:#fff;
}
*{box-sizing:border-box;margin:0;padding:0}
html,body{width:1200px;height:2274px;overflow:hidden}
body{font-family:'Lato',sans-serif;color:var(--text);background:var(--white);position:relative}
a{color:inherit;text-decoration:none}

/* top bar */
.topbar{position:absolute;left:0;top:0;width:1200px;height:40px;border-bottom:1px solid var(--line)}
.topbar .welcome{position:absolute;left:124px;top:14px;font-size:11px;color:var(--ink)}
.topbar .links{position:absolute;right:124px;top:13px;font-size:11.5px;color:var(--ink);display:flex}
.topbar .links span{padding:0 14px;border-left:1px solid var(--ink);line-height:12px}
.topbar .links span:first-child{border-left:none}
.topbar .links span:last-child{padding-right:0}

/* header */
.header{position:absolute;left:0;top:40px;width:1200px;height:136px;border:1px solid var(--line)}
.brand{position:absolute;left:124px;top:33px;display:flex;align-items:center;gap:10px}
.brand-dot{width:64px;height:64px;border-radius:50%;background:var(--green)}
.brand-name{font-weight:700;font-size:34px;color:var(--green)}
.tagline{position:absolute;left:323px;top:36px}
.tagline h1{font-family:'Josefin Sans',sans-serif;font-weight:300;font-size:35px;letter-spacing:3px;color:var(--ink)}
.tagline p{font-family:'Josefin Sans',sans-serif;font-weight:300;font-size:16.5px;color:var(--ink);margin-top:6px}
.contact{position:absolute;left:930px;top:42px;font-size:14px;color:#555;line-height:18px}
.contact .row{display:flex;gap:10px;align-items:flex-start}
.contact .row+.row{margin-top:16px}
.contact svg{flex:none;margin-top:1px}

/* service nav */
.service-nav{position:absolute;left:0;top:176px;width:1200px;height:84px;border-bottom:1px solid var(--line)}
.service-nav ul{list-style:none;position:absolute;left:124px;top:34px;width:952px;display:flex;justify-content:space-between;font-size:11px;color:var(--green)}
.service-nav li{line-height:12px}
.service-nav li.sep{color:#999}

/* hero */
.hero{position:absolute;left:0;top:260px;width:1200px;height:394px}
.hero h2{position:absolute;left:124px;top:92px;font-weight:400;font-size:32.5px;line-height:41px;color:var(--green)}
.btn-read{position:absolute;left:124px;top:247px;width:138px;height:42px;border-radius:21px;background:var(--green);color:var(--white);font-size:13px;display:flex;align-items:center;justify-content:center;gap:6px}
.hero-visual{position:absolute;left:560px;top:12px;width:610px;height:360px;border-radius:24px;background:linear-gradient(135deg,#e4e6e8 0%,#c9cdd1 55%,#4c7fc0 100%)}

/* services */
.services{position:absolute;left:0;top:654px;width:1200px;height:685px;background:var(--grey-bg);border-top:1px solid var(--line)}
.card{position:absolute;width:300px;height:285px;border-radius:8px;background:var(--white);overflow:hidden}
.card .head{height:98px;background:var(--green);display:flex;justify-content:center;padding-top:20px}
.card .body{position:absolute;left:0;top:95px;width:300px;height:190px;background:var(--white);border-radius:14px 14px 8px 8px;padding:30px 18px 0 17px}
.card h3{font-size:22px;font-weight:700;color:var(--green)}
.card p{width:255px;font-size:11.5px;line-height:14px;color:var(--ink);margin-top:12px}
.btn-more{position:absolute;left:17px;top:131px;width:110px;height:38px;border-radius:6px;background:var(--green);display:flex;overflow:hidden}
.btn-more span{flex:1;color:var(--white);font-weight:700;font-size:13px;display:flex;align-items:center;padding-left:16px}
.btn-more i{width:40px;background:var(--btn-dark);border-radius:6px;display:flex;align-items:center;justify-content:center}

/* features */
.features{position:absolute;left:0;top:1339px;width:1200px;height:404px}
.feature{position:absolute;width:464px;height:118px;border-bottom:1px solid var(--line)}
.feature .num{position:absolute;left:0;top:40px;width:58px;height:58px;border-radius:50%;background:var(--green);color:var(--white);font-size:34px;display:flex;align-items:center;justify-content:center}
.feature h4{position:absolute;left:69px;top:40px;font-size:18px;font-weight:700;color:var(--ink)}
.feature p{position:absolute;left:69px;top:67px;width:392px;font-size:10.8px;line-height:14px;color:var(--ink)}
.feature .more{position:absolute;left:69px;top:99px;font-size:13px;font-weight:700;color:var(--green);display:flex;gap:6px;align-items:center}

/* quote */
.quote{position:absolute;left:0;top:1743px;width:1200px;height:410px;background:var(--charcoal)}
.quote h3{position:absolute;top:32px;font-size:23px;font-weight:700;color:var(--white)}
.quote .intro{position:absolute;left:124px;width:383px;font-size:17px;line-height:18px;font-weight:300;color:#eee;text-align:justify}
.quote .intro.first{top:89px}
.quote .intro.second{top:160px;text-align:left}
.social{position:absolute;left:124px;top:253px;display:flex;gap:19px}
.social span{width:49px;height:49px;border-radius:50%;background:var(--green)}
.field{position:absolute;height:34px;border:1px solid #ddd;color:var(--white);font-size:12px;padding:10px 9px}
.send{position:absolute;left:755px;top:274px;width:105px;height:32px;border-radius:16px;background:var(--green);color:var(--white);font-size:13px;font-weight:700;font-style:italic;display:flex;align-items:center;justify-content:center}

/* footer */
.footer-nav{position:absolute;left:0;top:2153px;width:1200px;height:63px;background:var(--green)}
.footer-nav ul{list-style:none;position:absolute;left:124px;top:26px;width:952px;display:flex;justify-content:space-between;font-size:10.5px;color:var(--white)}
.footer-nav li{line-height:11px}
.copyright{position:absolute;left:0;top:2216px;width:1200px;height:58px;background:var(--charcoal-dark);color:#999;font-size:12.5px;display:flex;align-items:center;justify-content:center}
</style>
</head>
<body>

<div class="topbar">
  <div class="welcome">Wel come to our site...!</div>
  <nav class="links"><span>HOME</span><span>ABOUT US</span><span>CONTCT</span><span>FREE QUOTE</span></nav>
</div>

<header class="header">
  <div class="brand"><div class="brand-dot"></div><div class="brand-name">Inkvale</div></div>
  <div class="tagline">
    <h1>Duplication is our vocation</h1>
    <p>Professional photocopying - digital &amp; film processing, design and printing</p>
  </div>
  <div class="contact">
    <div class="row">
      <svg width="14" height="14" viewBox="0 0 24 24"><path fill="#666" d="M6.6 10.8a15.1 15.1 0 0 0 6.6 6.6l2.2-2.2c.3-.3.7-.4 1-.2 1.1.4 2.3.6 3.6.6.6 0 1 .4 1 1V20c0 .6-.4 1-1 1A17 17 0 0 1 3 4c0-.6.4-1 1-1h3.5c.6 0 1 .4 1 1 0 1.3.2 2.5.6 3.6.1.3 0 .7-.2 1z"/></svg>
      <span>07 555 0148</span>
    </div>
    <div class="row">
      <svg width="12" height="16" viewBox="0 0 12 16"><path fill="#666" d="M6 0a6 6 0 0 0-6 6c0 4.5 6 10 6 10s6-5.5 6-10a6 6 0 0 0-6-6zm0 8.2A2.2 2.2 0 1 1 6 3.8a2.2 2.2 0 0 1 0 4.4z"/></svg>
      <span>7/82 Alderbrook Road<br>&nbsp;&nbsp;Alderbrook - Harbourton</span>
    </div>
  </div>
</header>

<nav class="service-nav">
  <ul>
    <li>Photocopying</li><li class="sep">|</li><li>Printing</li><li class="sep">|</li><li>Laminating</li><li class="sep">|</li><li>Business cards</li><li class="sep">|</li><li>Typing services</li><li class="sep">|</li><li>Film processing</li><li class="sep">|</li><li>Photo Printing</li><li class="sep">|</li><li>Passport photos</li><li class="sep">|</li><li>Image Restoration</li><li class="sep">|</li><li>Printer Supplies</li>
  </ul>
</nav>

<section class="hero">
  <h2>Digital printing Laminating<br>Photocopying Services<br>Throughout Harbourton</h2>
  <a class="btn-read">READ MORE
    <svg width="12" height="12" viewBox="0 0 12 12"><circle cx="6" cy="6" r="6" fill="#fff"/><path d="M5 3.5 7.5 6 5 8.5" stroke="#7db135" stroke-width="1.6" fill="none"/></svg>
  </a>
  <div class="hero-visual" role="img" aria-label="Grey desktop laminator feeding out a laminated photo print"></div>
</section>

<section class="services">
  <article class="card" style="left:124px;top:44px">
    <div class="head">
      <svg width="80" height="60" viewBox="0 0 80 60" fill="none" stroke="#fff" stroke-width="3.5" stroke-linejoin="round"><path d="M40 6 72 20 40 34 8 20z"/><path d="M8 30l32 14 32-14"/><path d="M8 40l32 14 32-14"/><path d="M24 22l10-6 8 6 6-3 8 4"/></svg>
    </div>
    <div class="body"><h3>Photocopying</h3><p>Ex ea commodo consequat. Duis aute irure dolor in reprehenderie ctetur adipisicing elit sed iusmod tempor incididunt ut lab.</p>
      <a class="btn-more"><span>MORE</span><i><svg width="18" height="18" viewBox="0 0 18 18"><circle cx="9" cy="9" r="9" fill="#fff"/><path d="M7.5 5.5 11 9l-3.5 3.5" stroke="#2f3340" stroke-width="2" fill="none"/></svg></i></a></div>
  </article>
  <article class="card" style="left:450px;top:44px">
    <div class="head">
      <svg width="64" height="62" viewBox="0 0 64 62" fill="#fff"><path d="M18 4h40l-4 8H18z"/><rect x="4" y="18" width="52" height="26" rx="4"/><rect x="14" y="40" width="32" height="18" fill="#7db135" stroke="#fff" stroke-width="4"/><rect x="42" y="24" width="8" height="4" fill="#7db135"/></svg>
    </div>
    <div class="body"><h3>Laminating &amp; Binding</h3><p>Ex ea commodo consequat. Duis aute irure dolor in reprehenderie ctetur adipisicing elit sed iusmod tempor incididunt ut lab.</p>
      <a class="btn-more"><span>MORE</span><i><svg width="18" height="18" viewBox="0 0 18 18"><circle cx="9" cy="9" r="9" fill="#fff"/><path d="M7.5 5.5 11 9l-3.5 3.5" stroke="#2f3340" stroke-width="2" fill="none"/></svg></i></a></div>
  </article>
  <article class="card" style="left:776px;top:44px">
    <div class="head">
      <svg width="60" height="60" viewBox="0 0 60 60" fill="#fff"><path d="M16 2h28v18H16z"/><rect x="4" y="22" width="52" height="24" rx="3"/><rect x="14" y="40" width="32" height="18"/><rect x="20" y="8" width="20" height="2" fill="#7db135"/><rect x="20" y="13" width="20" height="2" fill="#7db135"/><rect x="10" y="40" width="40" height="2" fill="#7db135"/></svg>
    </div>
    <div class="body"><h3>Digital Printing</h3><p>Ex ea commodo consequat. Duis aute irure dolor in reprehenderie ctetur adipisicing elit sed iusmod tempor incididunt ut lab.</p>
      <a class="btn-more"><span>MORE</span><i><svg width="18" height="18" viewBox="0 0 18 18"><circle cx="9" cy="9" r="9" fill="#fff"/><path d="M7.5 5.5 11 9l-3.5 3.5" stroke="#2f3340" stroke-width="2" fill="none"/></svg></i></a></div>
  </article>
  <article class="card" style="left:124px;top:356px">
    <div class="head">
      <svg width="64" height="64" viewBox="0 0 64 64"><circle cx="32" cy="32" r="30" fill="#fff"/><circle cx="32" cy="32" r="6" fill="#7db135"/><path d="M29 26V6h6v20zM26.5 36.5 9 47l3-5.2L24 34zM37.5 36.5 55 47l-3-5.2L40 34z" fill="#7db135"/></svg>
    </div>
    <div class="body"><h3>Film Processing</h3><p>Ex ea commodo consequat. Duis aute irure dolor in reprehenderie ctetur adipisicing elit sed iusmod tempor incididunt ut lab.</p>
      <a class="btn-more"><span>MORE</span><i><svg width="18" height="18" viewBox="0 0 18 18"><circle cx="9" cy="9" r="9" fill="#fff"/><path d="M7.5 5.5 11 9l-3.5 3.5" stroke="#2f3340" stroke-width="2" fill="none"/></svg></i></a></div>
  </article>
  <article class="card" style="left:450px;top:356px">
    <div class="head">
      <svg width="70" height="54" viewBox="0 0 70 54" fill="none" stroke="#fff" stroke-width="4"><rect x="3" y="3" width="64" height="48" rx="7"/><path d="M13 22h20M13 32h20" stroke-width="4.5"/><rect x="40" y="16" width="16" height="22" rx="2" fill="#fff"/></svg>
    </div>
    <div class="body"><h3>Business Cards</h3><p>Ex ea commodo consequat. Duis aute irure dolor in reprehenderie ctetur adipisicing elit sed iusmod tempor incididunt ut lab.</p>
      <a class="btn-more"><span>MORE</span><i><svg width="18" height="18" viewBox="0 0 18 18"><circle cx="9" cy="9" r="9" fill="#fff"/><path d="M7.5 5.5 11 9l-3.5 3.5" stroke="#2f3340" stroke-width="2" fill="none"/></svg></i></a></div>
  </article>
  <article class="card" style="left:776px;top:356px">
    <div class="head">
      <svg width="70" height="60" viewBox="0 0 70 60" fill="#eaf3dc" stroke="#fff" stroke-width="3"><rect x="4" y="6" width="62" height="26" rx="6"/><path d="M18 28h34v18L42 56H18z"/><path d="M42 56V46h10"/><circle cx="14" cy="16" r="2" fill="#7db135" stroke="none"/><path d="M24 36h20M24 42h14" stroke="#7db135"/></svg>
    </div>
    <div class="body"><h3>Photo Printing</h3><p>Ex ea commodo consequat. Duis aute irure dolor in reprehenderie ctetur adipisicing elit sed iusmod tempor incididunt ut lab.</p>
      <a class="btn-more"><span>MORE</span><i><svg width="18" height="18" viewBox="0 0 18 18"><circle cx="9" cy="9" r="9" fill="#fff"/><path d="M7.5 5.5 11 9l-3.5 3.5" stroke="#2f3340" stroke-width="2" fill="none"/></svg></i></a></div>
  </article>
</section>

<section class="features">
  <div class="feature" style="left:124px;top:0">
    <div class="num">1</div><h4>Cost effective photocopying</h4>
    <p>No matter the quantity of photocopies you need or the size of your copy - you can rely on us to provide a top quality service!</p>
    <a class="more">MORE INFO <svg width="14" height="12" viewBox="0 0 14 12"><path d="M8 0l6 5-6 5V7C4 7 1.5 8.5 0 12 0 7 3 3.5 8 3z" fill="#7db135"/></svg></a>
  </div>
  <div class="feature" style="left:611px;top:0">
    <div class="num">2</div><h4>Personal desktop publishing</h4>
    <p>From personalised brochures, posters and birthday and special occasion cards to top quality, cheap business cards - you get it all!</p>
    <a class="more">MORE INFO <svg width="14" height="12" viewBox="0 0 14 12"><path d="M8 0l6 5-6 5V7C4 7 1.5 8.5 0 12 0 7 3 3.5 8 3z" fill="#7db135"/></svg></a>
  </div>
  <div class="feature" style="left:124px;top:118px">
    <div class="num">3</div><h4>All digital format printing</h4>
    <p>Either email us your file or bring it into the store and we can get you the print you need. All prints are to the highest quality.</p>
    <a class="more">MORE INFO <svg width="14" height="12" viewBox="0 0 14 12"><path d="M8 0l6 5-6 5V7C4 7 1.5 8.5 0 12 0 7 3 3.5 8 3z" fill="#7db135"/></svg></a>
  </div>
  <div class="feature" style="left:611px;top:118px">
    <div class="num">4</div><h4>Film photo processing</h4>
    <p>Bring in your film to the store and we will work with you to get the best quality print for your purpose and needs. We work with it all!</p>
    <a class="more">MORE INFO <svg width="14" height="12" viewBox="0 0 14 12"><path d="M8 0l6 5-6 5V7C4 7 1.5 8.5 0 12 0 7 3 3.5 8 3z" fill="#7db135"/></svg></a>
  </div>
  <div class="feature" style="left:124px;top:236px">
    <div class="num">5</div><h4>Laminating and binding</h4>
    <p>Create a professional image for your documents or books. Lamination and binding also keeps your documents well protected!</p>
    <a class="more">MORE INFO <svg width="14" height="12" viewBox="0 0 14 12"><path d="M8 0l6 5-6 5V7C4 7 1.5 8.5 0 12 0 7 3 3.5 8 3z" fill="#7db135"/></svg></a>
  </div>
  <div class="feature" style="left:611px;top:236px">
    <div class="num">6</div><h4>Quality digital photo prints</h4>
    <p>Get your photo printed to your requirements - either from a file or from your digital camera. With a wide range of options you can get the print you want.</p>
    <a class="more">MORE INFO <svg width="14" height="12" viewBox="0 0 14 12"><path d="M8 0l6 5-6 5V7C4 7 1.5 8.5 0 12 0 7 3 3.5 8 3z" fill="#7db135"/></svg></a>
  </div>
</section>

<section class="quote">
  <h3 style="left:124px">Get a free quote</h3>
  <p class="intro first">...or talk to our team about your requirements. Please fill out the form below and we will contact you within a day.</p>
  <p class="intro second">You can now upload and send us your file for a free quote!</p>
  <div class="social"><span></span><span></span><span></span><span></span><span></span><span></span></div>

  <h3 style="left:531px">Equire Form</h3>
  <div class="field" style="left:531px;top:89px;width:267px">First Name</div>
  <div class="field" style="left:809px;top:89px;width:267px">Last Name</div>
  <div class="field" style="left:531px;top:132px;width:267px">Number</div>
  <div class="field" style="left:809px;top:132px;width:267px">Email</div>
  <div class="field" style="left:531px;top:175px;width:545px;height:89px">Message</div>
  <div class="send">SEND</div>
</section>

<nav class="footer-nav">
  <ul>
    <li>Home</li><li>|</li><li>About</li><li>|</li><li>Photocopying</li><li>|</li><li>Printing</li><li>|</li><li>Laminating</li><li>|</li><li>Business cards</li><li>|</li><li>Typing services</li><li>|</li><li>Film processing</li><li>|</li><li>Photo Printing</li><li>|</li><li>Passport photos</li><li>|</li><li>Image Restoration</li><li>|</li><li>Printer Supplies</li><li>|</li><li>Free quote</li><li>|</li><li>Contact</li>
  </ul>
</nav>
<div class="copyright">Inkvale © copyright 2015 • Privacy Policy</div>

</body>
</html>
```